business card

Business card for new business.
Red and black corporate colors.
Card can have an Indsutrial feel to it. Feel free to add Rust, Bolted steel, or graphics as you see fit. We provide highly specialized services to the below mentioned industries.
Keep information out of corners so that if I want I can choose rounded corners.
Information
- front. name - title - phone - email
- Rear
Processing - Transit - Civil Works - Quarrying - Power
Ashford - Bellmore - Crestvale Falls - Dunmere - Eastbrook

```html
<!DOCTYPE html>
<html lang="en">
<head>
<meta charset="utf-8">
<title>Framewell – Business Card</title>
<link href="https://fonts.googleapis.com/css2?family=Roboto:wght@300;400;500;700;900&display=swap" rel="stylesheet">
<style>
  :root {
    --red: #ec1c24;
    --white: #ffffff;
    --grey: #6d6e71;
    --grey-box: #808184;
    --backdrop: #3b3b3b;
    --backdrop-light: #4a4a4a;
  }
  * { box-sizing: border-box; margin: 0; padding: 0; }
  html, body { width: 1200px; height: 900px; overflow: hidden; }
  body {
    background: radial-gradient(ellipse at 50% 55%, var(--backdrop-light), var(--backdrop) 70%);
    font-family: "Roboto", Arial, sans-serif;
    position: relative;
  }
  .card {
    position: absolute;
    top: 296px;
    width: 540px;
    height: 309px;
    border-radius: 24px;
    overflow: hidden;
    box-shadow: 0 14px 30px rgba(0,0,0,.45);
    background: var(--red);
  }
  .card--front { left: 40px; }
  .card--back  { left: 620px; }

  .brand {
    position: absolute;
    display: flex; align-items: center; gap: 12px;
    font-weight: 900; text-transform: uppercase; letter-spacing: 1px;
    line-height: 1; white-space: nowrap;
  }
  .brand__square { width: 18px; height: 18px; flex: none; }

  /* front */
  .front__upper {
    position: absolute; left: 0; top: 0; width: 100%; height: 140px;
    background: var(--white);
  }
  .card--front .brand { left: 190px; top: 48px; font-size: 44px; color: var(--grey); }
  .card--front .brand__square { background: var(--red); }

  .name-box {
    position: absolute; left: 140px; top: 118px;
    width: 200px; height: 58px;
    background: var(--grey-box); color: var(--white);
    text-align: center; padding-top: 9px;
  }
  .name-box__name { font-size: 19px; font-weight: 400; letter-spacing: .5px; text-transform: uppercase; }
  .name-box__title { font-size: 13px; font-weight: 300; margin-top: 3px; }

  .contacts {
    position: absolute; left: 34px; top: 192px;
    list-style: none; color: var(--white);
    font-size: 13.5px; font-weight: 400; line-height: 19px;
  }
  .contacts li { display: flex; align-items: center; gap: 8px; }
  .contacts svg { width: 10px; height: 10px; flex: none; }

  .address {
    position: absolute; right: 40px; top: 238px;
    color: var(--white); font-size: 17px; line-height: 22px; font-weight: 400;
    font-style: normal;
  }

  /* back */
  .card--back .brand { left: 96px; top: 100px; font-size: 54px; color: var(--white); }
  .card--back .brand__square { background: var(--white); }
  .sectors {
    position: absolute; left: 60px; top: 186px;
    color: var(--white); font-size: 13.5px; font-weight: 300; line-height: 20px;
  }
  .sectors p:first-child { padding-left: 30px; }
</style>
</head>
<body>

<section class="card card--front" aria-label="Card front">
  <div class="front__upper"></div>
  <div class="brand"><span class="brand__square"></span><span>Framewell</span></div>
  <div class="name-box">
    <p class="name-box__name">Daniel Harper</p>
    <p class="name-box__title">Director</p>
  </div>
  <ul class="contacts">
    <li>
      <svg viewBox="0 0 10 10"><path d="M2 0.5 L3.6 2.8 L2.6 3.8 Q3.6 6 6.2 7.4 L7.2 6.4 L9.5 8 L8.4 9.5 Q4 9 0.5 1.6 Z" fill="#fff"/></svg>
      <span>+330 5172-4406</span>
    </li>
    <li>
      <svg viewBox="0 0 10 10"><rect x="0.5" y="2" width="9" height="6.5" fill="none" stroke="#fff" stroke-width="1"/><path d="M0.5 2 L5 5.6 L9.5 2" fill="none" stroke="#fff" stroke-width="1"/></svg>
      <span>info@framewell.com</span>
    </li>
    <li>
      <svg viewBox="0 0 10 10"><circle cx="5" cy="5" r="4.3" fill="none" stroke="#fff" stroke-width="1"/><ellipse cx="5" cy="5" rx="1.8" ry="4.3" fill="none" stroke="#fff" stroke-width=".8"/><line x1="0.7" y1="5" x2="9.3" y2="5" stroke="#fff" stroke-width=".8"/></svg>
      <span>www.framewell.com</span>
    </li>
  </ul>
  <address class="address">
    2150 Ridgeback Rd.<br>Redmarsh, AB T0K 4R2
  </address>
</section>

<section class="card card--back" aria-label="Card back">
  <div class="brand"><span class="brand__square"></span><span>Framewell</span></div>
  <div class="sectors">
    <p>Processing - Transit - Civil Works - Quarrying - Power</p>
    <p>Ashford - Bellmore - Crestvale Falls - Dunmere - Eastbrook</p>
  </div>
</section>

</body>
</html>
```